Structural Engineering Business Card

Brookvane Drafting does residential house plans for clients in Central Florida. Would like simple but elegant business card that is appropriate for a house plan engineering company. Prefer black business card with black/white them but open to other shades of blue. I uploaded a sample card that I came across that looked good but please come up with your own creative designs.

Contact Information for Business Card

Name, Title, Phone, Email, Address, website

```html
<!DOCTYPE html>
<html lang="en">
<head>
<meta charset="utf-8">
<title>Brookvane Drafting – Business Card</title>
<link rel="stylesheet" href="https://fonts.googleapis.com/css2?family=Poppins:wght@400;700&display=swap">
<style>
  :root {
    --backdrop: #2a2a2a;
    --card-light: #ffffff;
    --card-dark: #000000;
    --ink: #111111;
    --ink-soft: #2b2b2b;
    --paper: #ffffff;
  }
  * { margin: 0; padding: 0; box-sizing: border-box; }
  html, body {
    width: 1093px; height: 1200px; overflow: hidden;
    background: var(--backdrop);
    font-family: "Poppins", sans-serif;
  }
  .canvas { position: relative; width: 1093px; height: 1200px; }
  .card {
    position: absolute; left: 265px;
    width: 580px; height: 357px;
    border-radius: 24px; overflow: hidden;
  }
  .card--front { top: 226px; background: var(--card-light); color: var(--ink); }
  .card--back { top: 621px; background: var(--card-dark); color: var(--paper); }

  .holder { position: absolute; left: 37px; top: 58px; }
  .holder__name { font-weight: 700; font-size: 20px; line-height: 1.05; letter-spacing: 0.2px; }
  .holder__title { font-weight: 400; font-size: 16px; line-height: 1.1; color: var(--ink-soft); }

  .brand-name { font-weight: 700; white-space: nowrap; letter-spacing: 0.2px; }
  .card--front .brand-name {
    position: absolute; right: 32px; top: 80px; font-size: 23px; color: var(--ink);
  }
  .card--back .brand-name {
    position: absolute; left: 0; right: 0; top: 155px; text-align: center;
    font-size: 38px; color: var(--paper);
  }

  .contacts { position: absolute; left: 37px; top: 258px; list-style: none; }
  .contacts li {
    display: flex; align-items: center; gap: 8px;
    font-size: 16.5px; line-height: 21px; color: var(--ink);
  }
  .contacts svg { width: 15px; height: 15px; flex: none; }

  .address {
    position: absolute; right: 32px; top: 279px; text-align: right;
    font-style: normal; font-size: 16.5px; line-height: 21px; color: var(--ink);
  }
</style>
</head>
<body>
<main class="canvas">
  <section class="card card--front" aria-label="Business card front">
    <div class="holder">
      <p class="holder__name">DANIEL HARGROVE</p>
      <p class="holder__title">Managing Director</p>
    </div>
    <p class="brand-name">Brookvane Drafting</p>
    <ul class="contacts">
      <li>
        <svg viewBox="0 0 24 24" aria-hidden="true"><path fill="currentColor" d="M6.6 10.8a15.1 15.1 0 0 0 6.6 6.6l2.2-2.2c.3-.3.7-.4 1-.2 1.1.4 2.3.6 3.6.6.6 0 1 .4 1 1V20c0 .6-.4 1-1 1A17 17 0 0 1 3 4c0-.6.4-1 1-1h3.5c.6 0 1 .4 1 1 0 1.3.2 2.5.6 3.6.1.3 0 .7-.2 1z"/></svg>
        044-555 010 234
      </li>
      <li>
        <svg viewBox="0 0 24 24" aria-hidden="true"><path fill="currentColor" d="M2 5h20v14H2z"/><path fill="none" stroke="#fff" stroke-width="1.8" d="M2.5 5.8 12 13l9.5-7.2"/></svg>
        info@brookvane.com
      </li>
      <li>
        <svg viewBox="0 0 24 24" aria-hidden="true"><g fill="none" stroke="currentColor" stroke-width="1.8"><circle cx="12" cy="12" r="9.5"/><ellipse cx="12" cy="12" rx="4" ry="9.5"/><path d="M2.5 12h19M4 7h16M4 17h16"/></g></svg>
        www.brookvanedrafting.com
      </li>
    </ul>
    <address class="address">
      418, Cypress Ridge Lane<br>
      32801, Orlando FL
    </address>
  </section>

  <section class="card card--back" aria-label="Business card back">
    <p class="brand-name">Brookvane Drafting</p>
  </section>
</main>
</body>
</html>
```